Business Card Design Can you design a business card design? Looking for something unique and differe

Can you design a business card design? Looking for something unique and different. Can you design a business card design? Looking for something unique and different.Can you design a business card design? Looking for something unique and different.Can you design a business card design? Looking for something unique and different.Can you design a business card design? Looking for something unique and different.Can you design a business card design? Looking for something unique and different.

Industry/Entity Type

Business

Contact Information for Business Card

Can you design a business card design? Looking for something unique and different.

Font styles to use
Serif

```html
<!DOCTYPE html>
<html lang="en">
<head>
<meta charset="utf-8">
<title>Dosewell Business Card</title>
<link rel="stylesheet" href="https://fonts.googleapis.com/css2?family=Lato:wght@400;700&display=swap">
<style>
  :root {
    --backdrop: #2e2e2e;
    --card: #1c1c1d;
    --white: #f4f4f4;
    --purple: #a885cc;
    --grey: #9d9d9d;
    --divider: #3a3a3b;
  }
  * { margin: 0; padding: 0; box-sizing: border-box; }
  html, body {
    width: 1200px; height: 900px; overflow: hidden;
    background: var(--backdrop);
    font-family: "Lato", sans-serif;
  }
  .canvas {
    position: relative; width: 1200px; height: 900px;
    display: flex; align-items: center; justify-content: center; gap: 50px;
  }
  .card {
    width: 500px; height: 290px;
    background: var(--card);
    border-radius: 22px;
    position: relative;
  }
  .card-front { display: flex; align-items: center; }
  .brand-block {
    width: 220px; height: 100%;
    display: flex; align-items: center; justify-content: center; gap: 12px;
  }
  .brand-square {
    width: 22px; height: 22px; background: var(--purple);
  }
  .brand-name {
    font-family: "Lato", sans-serif;
    font-weight: 700; font-size: 34px; color: var(--purple);
  }
  .divider {
    width: 1px; height: 190px; background: var(--divider);
  }
  .contact { padding-left: 24px; color: var(--white); }
  .person-name { font-size: 23px; font-weight: 400; line-height: 1.1; }
  .person-role { font-size: 15px; color: var(--purple); margin-bottom: 14px; }
  .address { font-size: 15px; line-height: 1.3; margin-bottom: 14px; }
  .details { list-style: none; font-size: 15px; line-height: 1.35; }
  .details .label { color: var(--purple); margin-right: 4px; }
  .card-back {
    display: flex; align-items: center; justify-content: center; gap: 14px;
  }
  .card-back .brand-name { font-size: 42px; }
  .card-back .brand-square { width: 26px; height: 26px; }
</style>
</head>
<body>
  <main class="canvas">
    <section class="card card-front">
      <div class="brand-block">
        <span class="brand-square"></span>
        <span class="brand-name">Dosewell</span>
      </div>
      <div class="divider"></div>
      <div class="contact">
        <p class="person-name">Daniel Reyes</p>
        <p class="person-role">Managing Director</p>
        <p class="address">48, Harbour Lane Suite 2<br>Eastmere Bay, 560214.</p>
        <ul class="details">
          <li><span class="label">T:</span>044-987 654 321</li>
          <li><span class="label">E:</span>hello@dosewell.com</li>
          <li><span class="label">W:</span>www.dosewellcare.com</li>
        </ul>
      </div>
    </section>
    <section class="card card-back">
      <span class="brand-square"></span>
      <span class="brand-name">Dosewell</span>
    </section>
  </main>
</body>
</html>
```